Agriculture Security Company needs a business card design

We need a business card design for a new company based in Seattle calls Ferncrest Guardline LLC. We provide high-end physical security solutions that is geared and focused towards to the marijuana grow operations, wholesalers and distributors. We DO NOT get involved in the retail operations (store fronts). We would like to see designs that incorporate professionalism, reliability, trustworthy and forward thinking as traits of our organization.

Industry/Entity Type

Security

```html
<!DOCTYPE html>
<html lang="en">
<head>
<meta charset="utf-8">
<title>Ferncrest Guardline LLC — Business Card</title>
<link rel="stylesheet" href="https://fonts.googleapis.com/css2?family=Open+Sans:wght@400;600;700&display=swap">
<style>
  :root {
    --backdrop: #e9e6df;
    --card-white: #ffffff;
    --card-green: #0f6a37;
    --brand-green: #2f8a3f;
    --title-green: #7fb341;
    --body-grey: #454545;
    --rule-start: #2f8a3f;
    --rule-end: rgba(47, 138, 63, 0);
    --back-text: #dfeee3;
  }
  * { box-sizing: border-box; margin: 0; padding: 0; }
  html, body {
    width: 1200px; height: 1023px; overflow: hidden;
    background: var(--backdrop);
    font-family: "Open Sans", Arial, sans-serif;
  }
  .sheet {
    width: 1200px; height: 1023px;
    display: flex; flex-direction: column;
    align-items: center; justify-content: center; gap: 48px;
  }
  .card {
    width: 770px; height: 440px;
    border-radius: 4px;
    box-shadow: 0 6px 20px rgba(0,0,0,0.18);
    position: relative; overflow: hidden;
  }
  /* Front */
  .card-front { background: var(--card-white); display: flex; }
  .front-brand {
    width: 46%;
    display: flex; align-items: center; justify-content: center;
  }
  .brand-name {
    font-weight: 600; color: var(--brand-green);
    font-size: 30px; line-height: 1.15; text-align: center;
    letter-spacing: 0.5px;
  }
  .front-divider {
    width: 2px; margin: 60px 0;
    background: linear-gradient(to bottom, var(--rule-end), var(--rule-start) 50%, var(--rule-end));
  }
  .front-details {
    flex: 1; padding: 78px 0 0 44px;
    color: var(--body-grey);
  }
  .person-name { font-weight: 700; font-size: 30px; color: var(--brand-green); line-height: 1.1; }
  .person-title { font-size: 17px; color: var(--title-green); margin-top: 2px; }
  .company-name { font-weight: 600; font-size: 17px; color: var(--brand-green); margin-top: 26px; }
  .address { font-size: 16px; line-height: 1.45; }
  .contact-list { list-style: none; margin-top: 26px; font-size: 16px; line-height: 1.7; }
  .contact-list li { display: flex; align-items: center; gap: 12px; }
  .contact-list svg { width: 16px; height: 16px; fill: var(--brand-green); flex: none; }
  /* Back */
  .card-back { background: var(--card-green); display: flex; align-items: center; justify-content: center; }
  .back-brand { font-weight: 600; font-size: 44px; color: var(--card-white); letter-spacing: 1px; text-align: center; line-height: 1.15; }
  .back-web {
    position: absolute; left: 36px; top: 50%;
    transform: translate(-50%, -50%) rotate(90deg) translateY(-50%);
    transform-origin: center;
    font-size: 15px; letter-spacing: 3px; color: var(--back-text);
    white-space: nowrap;
  }
</style>
</head>
<body>
<main class="sheet">
  <section class="card card-front" aria-label="Card front">
    <div class="front-brand">
      <p class="brand-name">Ferncrest<br>Guardline</p>
    </div>
    <div class="front-divider"></div>
    <div class="front-details">
      <p class="person-name">Dale Harmon</p>
      <p class="person-title">President</p>
      <p class="company-name">Ferncrest Guardline LLC</p>
      <p class="address">2180 Alder Point Rd<br>Bellmont, WA 98107</p>
      <ul class="contact-list">
        <li>
          <svg viewBox="0 0 16 16" aria-hidden="true"><path d="M3.5 1l2.6 2.8-1.3 1.8c.9 2 2.5 3.6 4.6 4.6l1.8-1.3L14 11.5 12.4 14C6.5 13.6 2.4 9.5 2 3.6z"/></svg>
          111-555-0142
        </li>
        <li>
          <svg viewBox="0 0 16 16" aria-hidden="true"><path d="M1 3h14v10H1z M1.5 3.5L8 9l6.5-5.5" fill="var(--brand-green)"/><path d="M1.5 3.8L8 9l6.5-5.2" fill="none" stroke="#fff" stroke-width="1.2"/></svg>
          info@ferncrestguardline.com
        </li>
        <li>
          <svg viewBox="0 0 16 16" aria-hidden="true"><circle cx="8" cy="8" r="7"/><path d="M1 8h14M8 1c-3 3.5-3 10.5 0 14M8 1c3 3.5 3 10.5 0 14" fill="none" stroke="#fff" stroke-width="1"/></svg>
          www.ferncrestguardline.com
        </li>
      </ul>
    </div>
  </section>

  <section class="card card-back" aria-label="Card back">
    <p class="back-web">www.ferncrestguardline.com</p>
    <p class="back-brand">Ferncrest<br>Guardline</p>
  </section>
</main>
</body>
</html>
```